Basic business card

use my newly created logo - and the phrases (Lower Cost of Test & Accelarated New Product Introduction) - and my new email domain / ID - use at conferences / tradeshows

Industry/Entity Type

semiconductor

Contact Information for Business Card

Daniel K Forde, Owner, communicate via Logo - Lower COT - Cost of Test, Accelerated NPI - New Product Introduction, phone +1 555 613 0946, Chandler, Arizona, USA, daniel.forde@qal-vub.com

Font styles to use
Sans Serif

Requirements
Nice to have
• re-use my logo created via Pixel Harbor last August (#7315926)

```html
<!DOCTYPE html>
<html lang="en">
<head>
<meta charset="utf-8">
<title>QAL-VUB Business Card</title>
<link href="https://fonts.googleapis.com/css2?family=Open+Sans:wght@400;600;700&display=swap" rel="stylesheet">
<style>
  :root{
    --bg:#232323;
    --card:#1f1f23;
    --silver:#a3abb8;
    --white:#ffffff;
    --orange:#f7931e;
    --blue:#0f75bd;
    --green:#7dc242;
    --slate:#4a5468;
  }
  *{margin:0;padding:0;box-sizing:border-box}
  html,body{width:1200px;height:780px;overflow:hidden;background:var(--bg);font-family:'Open Sans',sans-serif}
  .card{position:absolute;width:540px;height:310px;background:var(--card);border-radius:4px;box-shadow:0 18px 40px rgba(0,0,0,.55);overflow:hidden}
  .card--front{left:40px;top:235px}
  .card--back{left:620px;top:235px}

  .wordmark{position:absolute;display:flex;align-items:center;gap:14px;color:var(--silver);font-weight:600;letter-spacing:3px}
  .card--front .wordmark{left:0;right:0;top:0;bottom:0;justify-content:center;font-size:46px}
  .wordmark__square{width:26px;height:26px;background:var(--slate)}
  .card--back .wordmark{left:34px;top:118px;font-size:30px;letter-spacing:2px}
  .card--back .wordmark__square{width:20px;height:20px}

  .swoosh{position:absolute;left:0;top:0;width:540px;height:310px}

  .divider{position:absolute;left:292px;top:62px;width:2px;height:150px;background:var(--white)}

  .contact{position:absolute;left:314px;top:60px;color:var(--white)}
  .contact__name{font-size:22px;font-weight:700;line-height:1.1}
  .contact__first{color:var(--orange)}
  .contact__last{color:var(--blue)}
  .contact__title{font-size:11.5px;font-weight:600;margin-top:3px}
  .contact__address{font-size:11px;margin-top:12px;line-height:1.45}
  .contact__list{list-style:none;margin-top:10px;font-size:11px;line-height:1.65}
  .contact__list li{display:flex;align-items:center;gap:7px}
  .contact__list svg{width:11px;height:11px;flex:none}
</style>
</head>
<body>
  <section class="card card--front">
    <div class="wordmark"><span class="wordmark__square"></span>QAL-VUB</div>
  </section>

  <section class="card card--back">
    <svg class="swoosh" viewBox="0 0 540 310" aria-hidden="true">
      <path d="M0 236 C180 262 380 290 540 256 L540 310 L0 310 Z" fill="var(--green)"/>
      <path d="M300 272 C410 262 490 246 540 232 L540 242 C490 258 410 270 300 272 Z" fill="var(--blue)"/>
    </svg>
    <div class="wordmark"><span class="wordmark__square"></span>QAL-VUB</div>
    <div class="divider"></div>
    <div class="contact">
      <div class="contact__name"><span class="contact__first">Marta</span> <span class="contact__last">Kolarova</span></div>
      <div class="contact__title">Managing Director</div>
      <div class="contact__address">1840 Harbor Ridge Rd. Suite 310<br>Mesa Vista, TX 75001</div>
      <ul class="contact__list">
        <li><svg viewBox="0 0 24 24"><path fill="#7dc242" d="M6.6 10.8a15.1 15.1 0 0 0 6.6 6.6l2.2-2.2c.3-.3.7-.4 1-.2 1.1.4 2.3.6 3.6.6.6 0 1 .4 1 1V20c0 .6-.4 1-1 1A17 17 0 0 1 3 4c0-.6.4-1 1-1h3.5c.6 0 1 .4 1 1 0 1.3.2 2.5.6 3.6.1.3 0 .7-.2 1z"/></svg>(555) 204-7781</li>
        <li><svg viewBox="0 0 24 24"><path fill="#7dc242" d="M2 5h20v14H2zm2 2v.5l8 5 8-5V7zm0 2.8V17h16V9.8l-8 5z"/></svg>hello@qal-vub.com</li>
        <li><svg viewBox="0 0 24 24"><circle cx="12" cy="12" r="10" fill="#7dc242"/><path d="M2 12h20M12 2c3 3 3 17 0 20M12 2c-3 3-3 17 0 20" stroke="#1f1f23" stroke-width="1.5" fill="none"/></svg>www.qal-vub.com</li>
      </ul>
    </div>
  </section>
</body>
</html>
```